Irrigation Business needs their business cards modernised and revamped

I would like to keep my current logo, colours and revamp the format of the card.

I would like the card to be clean yet important.

Im not sure if you include texture but i would like the named logo to be indented into the card etc.

show me something alive and free something thats clinical to the point yet has a feel of achievement. i would like people to go nice card.

Target Market(s)

high end clients, corporate, sports field manger, the guys that make the decisions

Industry/Entity Type

Business

Contact Information for Business Card

nformation to be included

Dean Harlow (Director)
0487305526
dean@kolvat.biz
www.kestonfieldworks.com

instagram logo
google logo
facebook logo

Colors

Designer to choose colors to be used in the design.

Requirements
Nice to have
• indentations a really nice feel to the card good texture

```html
<!DOCTYPE html>
<html lang="en">
<head>
<meta charset="utf-8">
<title>Keston Fieldworks – Business Card</title>
<link href="https://fonts.googleapis.com/css2?family=Montserrat:wght@400;600&family=Open+Sans:wght@400&display=swap" rel="stylesheet">
<style>
  :root {
    --stage: #1d1d1f;
    --card-dark: #1a1a1b;
    --card-light: #ffffff;
    --brand-blue: #2f63b8;
    --sky-blue: #2ba3dc;
    --ink-grey: #6a6a6a;
    --muted-circle: #c9ced6;
  }
  * { box-sizing: border-box; margin: 0; padding: 0; }
  html, body { width: 1200px; height: 930px; overflow: hidden; }
  body { background: var(--stage); position: relative; font-family: "Montserrat", sans-serif; }

  .card {
    position: absolute;
    width: 520px;
    height: 300px;
    box-shadow: 0 18px 40px rgba(0,0,0,.55);
  }
  .card__frame {
    position: absolute;
    inset: 16px 20px;
    border: 1px solid var(--brand-blue);
  }

  /* Back */
  .card--back { left: 90px; top: 110px; background: var(--card-dark); }
  .brand-lockup {
    position: absolute; inset: 0;
    display: flex; flex-direction: column; align-items: center; justify-content: center; gap: 14px;
  }
  .brand-lockup__mark {
    width: 70px; height: 70px; border-radius: 50%;
    background: var(--sky-blue);
  }
  .brand-lockup__name {
    font-weight: 600; font-size: 24px; letter-spacing: .5px;
    color: var(--brand-blue); text-transform: uppercase;
  }

  /* Front */
  .card--front { left: 590px; top: 500px; background: var(--card-light); }
  .front-mark {
    position: absolute; left: 120px; top: 92px;
    width: 112px; height: 112px; border-radius: 50%;
    background: var(--sky-blue);
  }
  .divider {
    position: absolute; left: 280px; top: 78px;
    width: 1px; height: 108px; background: var(--sky-blue);
  }
  .contact { position: absolute; left: 300px; top: 74px; }
  .contact__name {
    font-weight: 600; font-size: 17px; color: var(--brand-blue);
    text-transform: uppercase; letter-spacing: .3px;
  }
  .contact__title {
    font-family: "Open Sans", sans-serif; font-size: 12px; color: var(--ink-grey);
    margin-top: 2px; margin-bottom: 10px;
  }
  .contact__row {
    display: flex; align-items: center; gap: 8px;
    font-family: "Open Sans", sans-serif; font-size: 11.5px; color: var(--ink-grey);
    line-height: 19px;
  }
  .contact__row svg { width: 11px; height: 11px; flex: none; }
  .social {
    position: absolute; left: 260px; top: 212px;
    display: flex; gap: 6px;
  }
  .social__dot { width: 14px; height: 14px; border-radius: 50%; background: var(--muted-circle); }
</style>
</head>
<body>

<section class="card card--back" aria-label="Card back">
  <div class="card__frame"></div>
  <div class="brand-lockup">
    <div class="brand-lockup__mark"></div>
    <div class="brand-lockup__name">Keston Fieldworks</div>
  </div>
</section>

<section class="card card--front" aria-label="Card front">
  <div class="card__frame"></div>
  <div class="front-mark"></div>
  <div class="divider"></div>
  <div class="contact">
    <div class="contact__name">Dean Harlow</div>
    <div class="contact__title">Director</div>
    <div class="contact__row">
      <svg viewBox="0 0 12 12"><path d="M3 1l2 2-1.2 1.4a6 6 0 0 0 3.8 3.8L9 7l2 2-1.5 2A9 9 0 0 1 1 2.5z" fill="#2ba3dc"/></svg>
      <span>0487305526</span>
    </div>
    <div class="contact__row">
      <svg viewBox="0 0 12 12"><rect x="0.5" y="2.5" width="11" height="7.5" fill="#2ba3dc"/><path d="M0.5 2.5l5.5 4 5.5-4" fill="none" stroke="#fff" stroke-width="1"/></svg>
      <span>dean@kolvat.biz</span>
    </div>
    <div class="contact__row">
      <svg viewBox="0 0 12 12"><g fill="none" stroke="#2ba3dc" stroke-width="1"><circle cx="6" cy="6" r="5"/><ellipse cx="6" cy="6" rx="2.2" ry="5"/><path d="M1 6h10M2 3.5h8M2 8.5h8"/></g></svg>
      <span>www.kestonfieldworks.com</span>
    </div>
  </div>
  <div class="social" aria-label="Social profiles">
    <span class="social__dot"></span>
    <span class="social__dot"></span>
    <span class="social__dot"></span>
  </div>
</section>

</body>
</html>
```